Merrow Trade finance web design

We are a newly established business which provides invoice finance to Small Businesses in England and Wales.
Our approach is very much a funder where the small business owner can talk to the decision maker. We will guarantee on receipt of information, a decision within 24 hours.
We are not a bank so the look of the website need to be friendly but professional.
Have two types of people we are trying to attract to the website: 1) partners who are small business owners and 2) introducers who is accountants and commercial brokers who introduce us to the small businesses.
Currently no website, although domain has been reserved.
The design should be:
Professional
“Clean” Look
Designed to convey Trust and Authority.
Appeal to the small business owner.
Must incorporate:
Logo (attached)
Front page:Top tabs to other pages 1) About us 2) Services 3) Introducers 4) Contact us
Need picture and logo on page.
1) About us page- Room for talk about the company, the people and our critera.
2) Services page- We need for what invoice finance is, and 5 boxes for different services we will provide. (link on page to contact us)
3) Introducers page- We need a part for why become an introducer? Who we can help? Why we are different? (link on page to contact us)
4) Contact us page- Office address, email, tel and if possible a map and a contact me part which will email direct to us.
Text will be provided for the design, if we can see the setup of the website we will provide a part for each of the pages to support.
Styles we think convey the correct image:
www.dornelcapital.example
www.plivanlend.example
www.quorbacredit.example
Target Market(s)
Small business owners
Industry/Entity Type
Finance
Number of Pages Required
5+ page
Look and feel

```html
<!DOCTYPE html>
<html lang="en">
<head>
<meta charset="utf-8">
<title>Merrow Trade Finance</title>
<link rel="stylesheet" href="https://fonts.googleapis.com/css2?family=Asap:ital,wght@0,400;0,500;1,400&family=Poiret+One&family=Cormorant+Garamond:ital,wght@1,400&display=swap">
<style>
:root{
  --red:#d9202b;
  --red-dark:#a5161d;
  --ink:#1f1f1f;
  --text:#444;
  --muted:#777;
  --line:#e2e2e2;
  --band:#ececec;
  --white:#fff;
  --num:#d9d9d9;
}
*{margin:0;padding:0;box-sizing:border-box}
html,body{width:1200px;height:2299px;overflow:hidden;background:var(--white)}
body{position:relative;font-family:"Asap",sans-serif;color:var(--text)}
.abs{position:absolute}

/* hero */
.hero{left:0;top:0;width:1200px;height:674px;overflow:hidden}
.hero-photo{left:0;top:0;width:1200px;height:674px;
  background:linear-gradient(100deg,#eef3f8 0%,#e6edf4 30%,#c9d6e3 45%,#b7a79c 58%,#8ea4c0 66%,#e7e2dc 80%,#8c8a86 100%)}
.hero-shape{left:0;top:0}
.brand{left:74px;top:30px;display:flex;align-items:center;gap:12px;color:var(--white);font-size:34px;font-weight:500;letter-spacing:.5px}
.brand-mark{width:14px;height:14px;border-radius:50%;background:var(--white)}
.nav{left:414px;top:28px;display:flex;gap:0;font-size:15px;color:var(--white);text-transform:uppercase}
.nav a{color:inherit;text-decoration:none;margin-right:35px}
.phone{left:972px;top:25px;color:var(--white);font-size:19px;font-weight:500;display:flex;align-items:center;gap:8px}
.hero-lead{left:185px;top:411px;width:380px;font-size:23px;line-height:33px;color:var(--ink)}
.hero-promise{left:185px;top:530px;width:320px;font-size:16.5px;line-height:25px;font-style:italic;color:var(--red)}
.btn{display:inline-block;background:var(--red);color:var(--white);border-radius:20px;text-align:center;font-size:17px;text-decoration:none}
.hero-cta{left:185px;top:599px;width:183px;height:35px;line-height:35px}
.dots{left:1051px;top:638px;display:flex;gap:4px}
.dots span{width:11px;height:11px;border-radius:50%;background:rgba(255,255,255,.55)}
.dots span:first-child{background:var(--white)}

/* introducer band */
.intro-band{left:0;top:674px;width:1200px;height:92px;background:var(--band)}
.intro-band p{position:absolute;left:72px;top:22px;font-size:18px;color:var(--ink)}
.intro-cta{left:854px;top:28px;width:230px;height:35px;line-height:35px}

/* section heads */
.sec-title{left:0;width:1200px;text-align:center;font-family:"Poiret One",sans-serif;font-size:30px;color:var(--ink);letter-spacing:.5px}
.sec-sub{left:0;width:1200px;text-align:center;font-size:16px;color:var(--text)}

/* services */
.services{left:55px;top:932px;width:1095px;display:flex}
.service{width:219px;height:248px;text-align:center;border-right:1px solid var(--line);padding-top:3px}
.service:last-child{border-right:none}
.service svg{display:block;margin:0 auto;stroke:#8a8a8a;fill:none;stroke-width:2}
.service h3{font-weight:400;font-size:18px;color:var(--ink);margin-top:40px}
.service p{font-size:13.5px;line-height:20px;margin:12px auto 0;width:192px;color:var(--text)}
.more{font-size:12px;color:var(--muted);margin-top:16px;display:flex;align-items:center;justify-content:center;gap:4px}
.more i{width:10px;height:10px;border:1px solid var(--muted);border-radius:50%;display:inline-block}
.rule{left:74px;width:1052px;height:1px;background:var(--line)}

/* about */
.about-photo{left:74px;top:1330px;width:539px;height:310px;
  background:linear-gradient(120deg,#2b3440 0%,#5a6674 35%,#9b8c7c 60%,#6a5d52 85%,#3a3a3a 100%)}
.about-photo::after{content:"";position:absolute;left:10px;top:10px;right:10px;bottom:10px;border:2px solid rgba(255,255,255,.9)}
.about-title{left:670px;top:1325px;font-family:"Poiret One",sans-serif;font-size:30px;color:var(--ink)}
.about-copy{left:670px;top:1376px;width:460px;font-size:13.5px;line-height:22px;color:var(--text)}
.about-copy p+p{margin-top:20px}
.about-more{left:670px;top:1604px;justify-content:flex-start}

/* why */
.why{left:74px;top:1880px;display:flex;gap:0}
.why-item{width:360px;display:flex}
.why-num{font-family:"Cormorant Garamond",serif;font-style:italic;font-size:86px;line-height:70px;color:var(--num);width:99px}
.why-item h3{font-weight:400;font-size:19px;color:var(--ink);margin-top:12px}
.why-item p{font-size:13.5px;line-height:20.5px;margin-top:8px;width:230px}

/* footer */
.footer{left:0;top:2054px;width:1200px;height:245px;background:var(--band)}
.foot-head{font-family:"Poiret One",sans-serif;font-size:18px;color:var(--ink);position:absolute}
.foot-text{position:absolute;font-size:13.5px;line-height:22px;color:var(--text)}
.foot-divider{left:598px;top:49px;width:1px;height:92px;background:#d6d6d6}
.news-input{left:676px;top:92px;width:313px;height:46px;background:var(--white);font-size:13.5px;color:var(--muted);padding:14px 18px}
.news-btn{left:999px;top:92px;width:127px;height:46px;line-height:46px;border-radius:0;font-size:14px;text-transform:uppercase}
.foot-rule{left:74px;top:181px;width:1052px;height:1px;background:#d6d6d6}
.copyright{left:74px;top:206px;font-size:13.5px}
.connect{left:800px;top:206px;font-size:13.5px;width:109px}
.social{left:920px;top:194px;display:flex;gap:6px}
.social span{width:35px;height:35px;background:#bdbdbd}
</style>
</head>
<body>

<header class="abs hero">
  <div class="abs hero-photo" role="img" aria-label="Photo of a smiling young business couple at a desk in a bright office"></div>
  <svg class="abs hero-shape" width="1200" height="674" viewBox="0 0 1200 674" aria-hidden="true">
    <path d="M0 0H1200V48C900 70 560 150 290 260C170 310 70 380 0 450Z" fill="var(--red)"/>
    <path d="M0 0H1200V22C900 40 560 110 290 210C170 255 70 320 0 380Z" fill="var(--red-dark)"/>
  </svg>
  <div class="abs brand"><span class="brand-mark"></span>Merrow</div>
  <nav class="abs nav">
    <a href="#">Home</a><a href="#">About Us</a><a href="#">Services</a><a href="#">Introducers</a><a href="#">Contact Us</a>
  </nav>
  <div class="abs phone">
    <svg width="16" height="16" viewBox="0 0 24 24" aria-hidden="true"><path d="M6.6 10.8a15 15 0 0 0 6.6 6.6l2.2-2.2a1 1 0 0 1 1-.25 11.4 11.4 0 0 0 3.6.6 1 1 0 0 1 1 1V20a1 1 0 0 1-1 1A17 17 0 0 1 3 4a1 1 0 0 1 1-1h3.5a1 1 0 0 1 1 1c0 1.25.2 2.45.6 3.6a1 1 0 0 1-.25 1Z" fill="#fff"/></svg>
    1800 55 4120
  </div>
  <p class="abs hero-lead">Our approach is very much a funder where the small business owner can talk to the decision maker.</p>
  <p class="abs hero-promise">We will guarantee on receipt of information, a decision within 24 hours.</p>
  <a class="abs btn hero-cta" href="#">Contact Us Today!</a>
  <div class="abs dots"><span></span><span></span><span></span><span></span><span></span></div>
</header>

<section class="abs intro-band">
  <p>Lorem Ipsum is simply dummy text of the printing and typesetting industry.</p>
  <a class="abs btn intro-cta" href="#">Become An Introducer</a>
</section>

<h2 class="abs sec-title" style="top:815px">SERVICES WE PROVIDE</h2>
<p class="abs sec-sub" style="top:862px">Lorem Ipsum has been the industry's standard dummy text ever since the 1500s.</p>

<section class="abs services">
  <article class="service">
    <svg width="90" height="90" viewBox="0 0 90 90" aria-hidden="true"><path d="M8 78 28 58l12 10 30-34"/><path d="M58 34h12v12"/><circle cx="52" cy="66" r="12"/><path d="M52 60v12M48 63h6a3 3 0 0 1 0 6h-6"/><circle cx="40" cy="16" r="4"/><circle cx="30" cy="30" r="6"/></svg>
    <h3>Service Title</h3>
    <p>Lorem Ipsum is simply dummy text standard dummy text ever has been the industry.</p>
    <div class="more"><i></i>Read More</div>
  </article>
  <article class="service">
    <svg width="90" height="90" viewBox="0 0 90 90" aria-hidden="true"><path d="M30 84V68c-10-6-16-16-14-30C18 20 32 8 50 10c16 2 26 16 24 30l6 12h-6v10c0 4-3 6-7 6h-9v16"/><circle cx="40" cy="36" r="6"/><circle cx="58" cy="30" r="4"/><circle cx="54" cy="46" r="4"/></svg>
    <h3>Service Title</h3>
    <p>Lorem Ipsum is simply dummy text standard dummy text ever has been the industry.</p>
    <div class="more"><i></i>Read More</div>
  </article>
  <article class="service">
    <svg width="90" height="90" viewBox="0 0 90 90" aria-hidden="true"><path d="M30 8a12 12 0 0 0 0 24v50M30 32a12 12 0 0 0 0-24"/><path d="M22 84h16"/><circle cx="62" cy="60" r="16"/><path d="M62 44v16h16"/></svg>
    <h3>Service Title</h3>
    <p>Lorem Ipsum is simply dummy text standard dummy text ever has been the industry.</p>
    <div class="more"><i></i>Read More</div>
  </article>
  <article class="service">
    <svg width="90" height="90" viewBox="0 0 90 90" aria-hidden="true"><rect x="28" y="8" width="54" height="36" rx="4"/><rect x="8" y="30" width="56" height="40" rx="4" fill="#fff"/><path d="M20 70v12l12-12M18 42h36M18 50h36M18 58h24"/></svg>
    <h3>Service Title</h3>
    <p>Lorem Ipsum is simply dummy text standard dummy text ever has been the industry.</p>
    <div class="more"><i></i>Read More</div>
  </article>
  <article class="service">
    <svg width="90" height="90" viewBox="0 0 90 90" aria-hidden="true"><circle cx="45" cy="45" r="12"/><path d="M40 8h10l2 10 8 4 8-6 8 8-6 8 4 8 10 2v10l-10 2-4 8 6 8-8 8-8-6-8 4-2 10H40l-2-10-8-4-8 6-8-8 6-8-4-8-10-2V40l10-2 4-8-6-8 8-8 8 6 8-4Z"/></svg>
    <h3>Service Title</h3>
    <p>Lorem Ipsum is simply dummy text standard dummy text ever has been the industry.</p>
    <div class="more"><i></i>Read More</div>
  </article>
</section>

<div class="abs rule" style="top:1255px"></div>

<div class="abs about-photo" role="img" aria-label="Photo of a team meeting around a table in an office"></div>
<h2 class="abs about-title">ABOUT OUR COMPANY</h2>
<div class="abs about-copy">
  <p>Lorem Ipsum is simply dummy text of the printing and typesetting industry. Lorem Ipsum has been the industry's standard dummy text ever since the 1500s, when an unknown printer took a galley of type and scrambled it to make a type specimen book.</p>
  <p>It was popularised in the 1960s with the release of Letraset sheets containing Lorem Ipsum passages, and more recently with desktop publishing software like Aldus PageMaker including versions of Lorem Ipsum.</p>
</div>
<div class="abs more about-more"><i></i>More Information About Company</div>

<div class="abs rule" style="top:1713px"></div>

<h2 class="abs sec-title" style="top:1780px">WHY WE ARE DIFFERENT?</h2>
<p class="abs sec-sub" style="top:1828px">Lorem Ipsum has been the industry's standard dummy text ever since the 1500s.</p>

<section class="abs why">
  <div class="why-item"><span class="why-num">01</span><div><h3>Over 50 years of experience</h3><p>Lorem Ipsum has been the industry's took a galley of type it to make a type specimen book.</p></div></div>
  <div class="why-item"><span class="why-num">02</span><div><h3>We fast, accuracy &amp; reliable</h3><p>Lorem Ipsum has been the industry's took a galley of type it to make a type specimen book.</p></div></div>
  <div class="why-item"><span class="why-num">03</span><div><h3>We are improving everyday</h3><p>Lorem Ipsum has been the industry's took a galley of type it to make a type specimen book.</p></div></div>
</section>

<footer class="abs footer">
  <h4 class="foot-head" style="left:74px;top:42px">GET IN TOUCH</h4>
  <p class="foot-text" style="left:74px;top:81px">Merrow Trade Finance Limited<br>228, Lorem ipsum dolor,<br>Dosis anet - 84589</p>
  <p class="foot-text" style="left:345px;top:81px">T: 1800 55 4120<br>E: info@merrowtrade.example</p>
  <div class="abs foot-divider"></div>
  <h4 class="foot-head" style="left:676px;top:42px">SUBSCRIBE OUR NEWSLETTER</h4>
  <div class="abs news-input">Email Address</div>
  <a class="abs btn news-btn" href="#">Subscribe</a>
  <div class="abs foot-rule"></div>
  <p class="abs copyright">Copyright © 2016 Merrow Trade Finance Limited. All Rights Reserved</p>
  <p class="abs connect">Connect With Us :</p>
  <div class="abs social"><span></span><span></span><span></span><span></span><span></span></div>
</footer>

</body>
</html>
```